Brivolt Technologies business card design

We need a business card designed with our new logo. it would be great if the card could communicate it is a technology based company.

Target Market(s)

system integrators

Industry/Entity Type

technology, IOT

Contact Information for Business Card

Name, designation, Address, telephone number, email address

Requirements
Must have
• logo and company name
Nice to have
• something to do with technology

```html
<!DOCTYPE html>
<html lang="en">
<head>
<meta charset="utf-8">
<title>Brivolt Technologies – Business Card</title>
<link href="https://fonts.googleapis.com/css2?family=Open+Sans:wght@400;700&display=swap" rel="stylesheet">
<style>
  :root {
    --bg: #3d3d3c;
    --card: #1a1a1a;
    --card-deep: #141414;
    --orange: #f28c13;
    --white: #ffffff;
    --text: #e4e4e4;
    --shade: #2c2c2c;
  }
  * { box-sizing: border-box; margin: 0; padding: 0; }
  html, body {
    width: 1200px; height: 801px; overflow: hidden;
    background: var(--bg);
    font-family: "Open Sans", Arial, sans-serif;
  }
  .stage {
    position: relative; width: 1200px; height: 801px;
    display: flex; align-items: center; justify-content: center; gap: 40px;
  }
  .card {
    position: relative;
    width: 540px; height: 309px;
    background: var(--card);
    border-bottom: 3px solid var(--orange);
    box-shadow: 0 12px 30px rgba(0,0,0,.35);
    overflow: hidden;
  }

  /* Front */
  .brand-lockup {
    position: absolute; left: 30px; top: 144px;
    display: flex; align-items: center; gap: 9px;
    white-space: nowrap;
  }
  .brand-mark { width: 14px; height: 14px; background: var(--orange); flex: none; }
  .brand-name {
    font-weight: 700; font-size: 18px; color: var(--white);
    letter-spacing: 0;
  }
  .divider {
    position: absolute; left: 284px; top: 52px;
    width: 2px; height: 200px; background: var(--orange);
  }
  .details {
    position: absolute; left: 302px; top: 52px;
    color: var(--text); font-size: 13px; line-height: 1.5;
    white-space: nowrap;
  }
  .person-name {
    color: var(--orange); font-weight: 700; font-size: 17px;
    letter-spacing: .3px;
  }
  .person-role { margin-bottom: 12px; }
  .address { margin-bottom: 14px; }
  .contact-list { list-style: none; }
  .contact-list li { display: flex; align-items: center; gap: 8px; }
  .contact-list svg { width: 11px; height: 11px; flex: none; }

  /* Back */
  .card-back { background: linear-gradient(160deg, var(--card-deep), var(--card)); }
  .brand-pattern {
    position: absolute; left: 30px; top: 40px; width: 230px; height: 240px;
    background: radial-gradient(ellipse at 50% 55%, var(--shade), transparent 70%);
  }
  .back-lockup { left: auto; right: 40px; top: auto; bottom: 70px; gap: 10px; }
  .back-lockup .brand-name { font-size: 30px; }
  .back-lockup .brand-mark { width: 20px; height: 20px; }
</style>
</head>
<body>
<main class="stage">
  <section class="card card-front" aria-label="Business card front">
    <div class="brand-lockup">
      <span class="brand-mark"></span>
      <span class="brand-name">Brivolt Technologies</span>
    </div>
    <div class="divider"></div>
    <div class="details">
      <p class="person-name">DANIEL ROYCE</p>
      <p class="person-role">President</p>
      <p class="address">1180 Harbor Crest Drive<br>Seacliff CA 90412</p>
      <ul class="contact-list">
        <li>
          <svg viewBox="0 0 12 12"><path d="M2 1l2.5 0 1 3-1.5 1a6 6 0 0 0 3 3l1-1.5 3 1V11.5A10 10 0 0 1 .5 1.5z" fill="var(--orange)"/></svg>
          555-310-4872
        </li>
        <li>
          <svg viewBox="0 0 12 12"><rect x="0.5" y="2" width="11" height="8" fill="var(--orange)"/><path d="M1 2.5l5 4 5-4" stroke="var(--card)" fill="none"/></svg>
          info@brivolttech.com
        </li>
        <li>
          <svg viewBox="0 0 12 12"><circle cx="6" cy="6" r="5.5" fill="var(--orange)"/><path d="M.5 6h11M6 .5c-3 3-3 8 0 11M6 .5c3 3 3 8 0 11" stroke="var(--card)" fill="none" stroke-width=".8"/></svg>
          www.brivolttech.com
        </li>
      </ul>
    </div>
  </section>

  <section class="card card-back" aria-label="Business card back">
    <div class="brand-pattern" role="img" aria-label="Faint dark brand decoration area"></div>
    <div class="brand-lockup back-lockup">
      <span class="brand-mark"></span>
      <span class="brand-name">Brivolt Technologies</span>
    </div>
  </section>
</main>
</body>
</html>
```